Business Card for Vorla Parts Wholesale supplier

Hi There! I need a new business card for our company. We are specialized in selling Vorla parts, mostly we sell new LCD screens for Zelnar and Drelks. I would like to see that back in the design.

You can find the colors and logo's on our website: www.hartuvo.nl

Industry/Entity Type

Business

Contact Information for Business Card

My Details:
Tobias Lindqvist

Phone: 0031687203316
E-mail: Tobias@hartuvo.nl

Slogan: "Because Quality Matters"

Font styles to use
Sans Serif

Colors

Designer to choose colors to be used in the design.

Requirements
Must have
• A Black backside with the Hartuvo logo on it. The front side should be clean with only my contact details.
• But I'm also open for something really different or awesome!
Nice to have
• Remember that we are in the parts & repairing industry, So i'll be handing those business cards mainly to repair companies. Maybe you can do something with that thought :)

```html
<!DOCTYPE html>
<html lang="en">
<head>
<meta charset="utf-8">
<title>Hartuvo Business Card</title>
<link href="https://fonts.googleapis.com/css2?family=Exo+2:wght@400;600;700&family=Source+Sans+3:wght@600&display=swap" rel="stylesheet">
<style>
  :root {
    --backdrop: #7a5538;
    --card-white: #ffffff;
    --card-black: #000000;
    --brand-orange: #f26b21;
    --ink: #111111;
    --ink-soft: #555555;
    --rule: #9a9a9a;
  }
  html, body {
    margin: 0;
    padding: 0;
    width: 1200px;
    height: 987px;
    overflow: hidden;
    background: var(--backdrop);
  }
  .canvas {
    position: relative;
    width: 1200px;
    height: 987px;
  }
  .card {
    position: absolute;
    left: 292px;
    width: 616px;
    height: 351px;
    overflow: hidden;
    box-shadow: 0 2px 6px rgba(0,0,0,0.35);
  }
  .card--front { top: 130px; background: var(--card-white); }
  .card--back  { top: 505px; background: var(--card-black); }

  .wordmark {
    position: absolute;
    display: flex;
    align-items: center;
    font-family: "Exo 2", sans-serif;
    font-weight: 600;
    line-height: 1;
  }
  .wordmark__dot {
    border-radius: 50%;
    background: var(--brand-orange);
    flex: none;
  }
  .card--front .wordmark {
    left: 314px; top: 55px;
    font-size: 52px;
    color: var(--ink);
    gap: 10px;
  }
  .card--front .wordmark__dot { width: 44px; height: 44px; }

  .card--back .wordmark {
    left: 0; right: 0; top: 145px;
    justify-content: center;
    font-size: 64px;
    color: var(--card-white);
    gap: 12px;
  }
  .card--back .wordmark__dot { width: 56px; height: 56px; }

  .holder-name {
    position: absolute;
    left: 46px; top: 205px;
    margin: 0;
    font-family: "Exo 2", sans-serif;
    font-weight: 700;
    font-size: 23px;
    color: var(--brand-orange);
  }
  .name-rule {
    position: absolute;
    left: 46px; top: 245px;
    width: 525px; height: 1px;
    background: var(--rule);
  }
  .contact {
    position: absolute;
    left: 46px;
    display: flex;
    align-items: center;
    gap: 7px;
    font-family: "Exo 2", sans-serif;
    font-weight: 400;
    font-size: 17px;
    color: var(--ink-soft);
  }
  .contact--phone { top: 258px; }
  .contact--email { top: 281px; font-size: 16px; }
  .contact svg { flex: none; }

  .footer-bands {
    position: absolute;
    left: 0; top: 312px;
  }
  .website {
    position: absolute;
    right: 45px; top: 318px;
    font-family: "Exo 2", sans-serif;
    font-size: 15px;
    letter-spacing: 4px;
    color: var(--card-white);
  }
  .tagline {
    position: absolute;
    left: 0; right: 0; top: 278px;
    margin: 0;
    text-align: center;
    font-family: "Source Sans 3", sans-serif;
    font-weight: 600;
    font-size: 20px;
    color: var(--brand-orange);
  }
</style>
</head>
<body>
<main class="canvas">
  <section class="card card--front" aria-label="Front of business card">
    <div class="wordmark"><span class="wordmark__dot"></span>hartuvo</div>

    <h1 class="holder-name">Tobias Lindqvist</h1>
    <div class="name-rule"></div>

    <div class="contact contact--phone">
      <svg width="15" height="15" viewBox="0 0 24 24" aria-hidden="true">
        <path fill="var(--brand-orange)" d="M6.6 10.8a15.1 15.1 0 0 0 6.6 6.6l2.2-2.2a1 1 0 0 1 1-.25 11.4 11.4 0 0 0 3.6.57 1 1 0 0 1 1 1V20a1 1 0 0 1-1 1A17 17 0 0 1 3 4a1 1 0 0 1 1-1h3.5a1 1 0 0 1 1 1c0 1.25.2 2.45.57 3.57a1 1 0 0 1-.25 1z"/>
      </svg>
      <span>0031687203316</span>
    </div>
    <div class="contact contact--email">
      <svg width="15" height="11" viewBox="0 0 15 11" aria-hidden="true">
        <rect width="15" height="11" fill="var(--brand-orange)"/>
        <path d="M0.5 0.8 L7.5 6 L14.5 0.8" fill="none" stroke="#fff" stroke-width="1.2"/>
      </svg>
      <span>Tobias@hartuvo.nl</span>
    </div>

    <svg class="footer-bands" width="616" height="39" viewBox="0 0 616 39" aria-hidden="true">
      <polygon points="0,16 336,16 328,25 0,25" fill="var(--brand-orange)"/>
      <polygon points="350,0 616,0 616,39 316,39" fill="var(--card-black)"/>
    </svg>
    <div class="website">www.hartuvo.nl</div>
  </section>

  <section class="card card--back" aria-label="Back of business card">
    <div class="wordmark"><span class="wordmark__dot"></span>hartuvo</div>
    <p class="tagline">Because Quality Matters</p>
  </section>
</main>
</body>
</html>
```